Help me make landing pages for my web application that are mobile friendly

I need to make 2 mobile friendly landing pages for an application. The 2 pages will be related. First I need a home page and then I need a working page. I do not want to change the color scheme or logos. Just layout and design.

```html
<!DOCTYPE html>
<html lang="en">
<head>
<meta charset="utf-8">
<title>Tandemline – Assignments</title>
<link href="https://fonts.googleapis.com/css2?family=Poppins:wght@400;500;600&display=swap" rel="stylesheet">
<style>
:root{
  --stage:#a3a3a3;
  --page:#f7f7f7;
  --white:#ffffff;
  --nav:#4a4a4a;
  --ink:#3a3a3a;
  --muted:#555;
  --cyan:#29a9d9;
  --brand:#6a4fc0;
  --icon:#6a55b5;
  --complete:#8c6fd3;
  --active:#1fbd2c;
  --canceled:#da1a1a;
  --line:#dcdcdc;
  --field:#f5f5f5;
  --pill:#dff1fa;
  --soft:#ececec;
}
*{box-sizing:border-box;margin:0;padding:0}
html,body{width:776px;height:1200px;overflow:hidden}
body{background:var(--stage);font-family:"Poppins",sans-serif;color:var(--ink);position:relative}
.screen{position:absolute;width:362px;background:var(--page);overflow:hidden}
.screen--list{left:21px;top:12px;height:977px}
.screen--detail{left:399px;top:12px;height:1140px}
.topbar{height:64px;background:var(--white);position:relative;display:flex;align-items:center;justify-content:center}
.menu-btn{position:absolute;left:16px;top:27px}
.brand{display:flex;align-items:center;gap:7px;font-size:21px;font-weight:500;color:var(--brand);letter-spacing:-.2px}
.brand-dot{width:18px;height:18px;border-radius:50%;background:var(--brand)}
.nav{height:28px;background:var(--nav);display:flex;font-size:8px;color:#fff;padding-left:4px}
.nav a{padding:0 12.5px;line-height:28px;color:#fff;text-decoration:none;position:relative}
.nav a.is-active{color:var(--cyan)}
.nav a.is-active::after{content:"";position:absolute;left:0;right:0;bottom:0;height:2px;background:var(--cyan)}
.page-title{font-size:11.5px;font-weight:600;margin:19px 0 0 15px;color:#444}
.card{position:absolute;left:15px;width:330px;background:var(--white);border-radius:8px;box-shadow:0 1px 4px rgba(0,0,0,.12)}
.assign{height:117px;padding:9px 13px 0 9px}
.card-head{display:flex;align-items:center;gap:7px;font-size:9px;font-weight:600;color:#444;height:14px}
.card-head::after{content:"";flex:1;height:1px;background:var(--line)}
.person{display:flex;align-items:center;margin-top:6px;height:24px;font-size:8px}
.avatar{width:23px;height:23px;border-radius:50%;background:linear-gradient(135deg,#9a8a7c,#4c4440);margin:0 8px 0 1px;flex:none}
.person .name{color:var(--cyan);font-weight:600;margin-right:3px}
.person .edit{margin-left:auto}
.row{display:flex;align-items:center;height:18px;font-size:7.5px}
.row:first-of-type{margin-top:1px}
.row svg{width:8px;margin:0 14px 0 8px;flex:none}
.row .label{font-weight:600;width:60px}
.row .val{color:var(--muted)}
.badge{display:inline-block;height:15px;line-height:15px;padding:0 6px;border-radius:8px;color:#fff;font-size:8px;margin-left:-4px}
.badge--complete{background:var(--complete)}
.badge--active{background:var(--active)}
.badge--canceled{background:var(--canceled)}
.time{margin-left:2px;font-size:8px}
.urlbar{position:absolute;left:15px;width:330px;height:31px;background:var(--nav);border-radius:16px;display:flex;align-items:center;justify-content:center;color:#fff;font-size:10px}
.urlbar .l{position:absolute;left:13px}
.urlbar .r{position:absolute;right:15px}
.panel{padding:9px 10px 0 10px}
.panel h2{font-size:11.5px;font-weight:500;color:#444;height:16px;line-height:16px}
.panel .rule{height:1px;background:var(--line);margin:7px 0 0 0}
.info{list-style:none;font-size:8px}
.info li{display:flex;align-items:center;height:22px;border-bottom:1px solid var(--line)}
.info li:last-child{border-bottom:none}
.info .k{width:185px;color:var(--cyan);font-weight:600}
.info .v{display:flex;align-items:center;gap:6px;white-space:nowrap}
.mini-avatar{width:19px;height:19px;border-radius:50%;background:linear-gradient(135deg,#8e7c70,#3e3733)}
.textbox{background:var(--field);border:1px solid #cfcfcf;border-radius:2px}
.pill{display:inline-flex;align-items:center;gap:4px;height:19px;padding:0 11px;border-radius:10px;font-size:7.5px}
.pill--blue{background:var(--pill);color:var(--cyan)}
.pill--gray{background:var(--soft);color:#666}
.field-label{font-size:7.5px;font-weight:600;margin-top:5px;height:12px;display:flex;align-items:center;gap:4px}
.input{height:22px;border:1px solid #cfcfcf;border-radius:2px;background:#fff;display:flex;align-items:center;padding:0 7px;font-size:8px;margin-top:2px}
.input svg{margin-left:auto}
.input .cb,.field-label .cb{width:6px;height:6px;border:1px solid #444;margin-right:5px;display:inline-block}
.meta{font-size:8px;margin-top:6px}
.meta b{font-weight:600}
.ok{color:var(--active)}
.actions{position:absolute;right:16px;display:flex;gap:3px}
.btn{height:18px;padding:0 10px;border-radius:9px;color:#fff;font-size:7.5px;display:flex;align-items:center;gap:3px}
.btn--save{background:var(--brand)}
.btn--close{background:#9b9b9b}
</style>
</head>
<body>

<section class="screen screen--list">
  <header class="topbar">
    <svg class="menu-btn" width="10" height="9" viewBox="0 0 10 9"><path d="M0 1h10M0 4.5h10M0 8h10" stroke="#333" stroke-width="1.5"/></svg>
    <div class="brand"><span class="brand-dot"></span>Tandemline</div>
  </header>
  <nav class="nav"><a>Home</a><a>Available Openings</a><a class="is-active">Assignments</a><a>Support</a></nav>
  <h1 class="page-title">My Assignments</h1>

  <article class="card assign" style="top:134px">
    <div class="card-head">Subbing For</div>
    <div class="person"><div class="avatar" role="img" aria-label="Staff member photo"></div><span class="name">Nora Ellisworth</span>(Teacher)<svg class="edit" width="7" height="7" viewBox="0 0 10 10"><path d="M1 9l1-3 5-5 2 2-5 5z" fill="var(--cyan)"/></svg></div>
    <div class="row"><svg viewBox="0 0 10 12"><path d="M5 0a4 4 0 014 4c0 3-4 8-4 8S1 7 1 4a4 4 0 014-4z" fill="var(--icon)"/><circle cx="5" cy="4" r="1.5" fill="#fff"/></svg><span class="label">Location:</span><span class="val">CHES</span></div>
    <div class="row"><svg viewBox="0 0 10 12"><path d="M1 0h5l3 3v9H1z" fill="var(--icon)"/></svg><span class="label">Status:</span><span class="badge badge--complete">Complete</span></div>
    <div class="row"><svg viewBox="0 0 10 10"><circle cx="5" cy="5" r="4" fill="none" stroke="var(--icon)" stroke-width="1.2"/><path d="M5 2.5V5l1.8 1" stroke="var(--icon)" fill="none"/></svg><span class="label">Time Slots:</span><span class="val time">09/02 – 09/02 (1h 0m)</span></div>
  </article>

  <article class="card assign" style="top:265px">
    <div class="card-head">Subbing For</div>
    <div class="person"><div class="avatar" role="img" aria-label="Staff member photo"></div><span class="name">Priyanka</span>&nbsp;Extra duty (Teacher)<svg class="edit" width="7" height="7" viewBox="0 0 10 10"><path d="M1 9l1-3 5-5 2 2-5 5z" fill="var(--cyan)"/></svg></div>
    <div class="row"><svg viewBox="0 0 10 12"><path d="M5 0a4 4 0 014 4c0 3-4 8-4 8S1 7 1 4a4 4 0 014-4z" fill="var(--icon)"/><circle cx="5" cy="4" r="1.5" fill="#fff"/></svg><span class="label">Location:</span><span class="val">CHES</span></div>
    <div class="row"><svg viewBox="0 0 10 12"><path d="M1 0h5l3 3v9H1z" fill="var(--icon)"/></svg><span class="label">Status:</span><span class="badge badge--complete">Complete</span></div>
    <div class="row"><svg viewBox="0 0 10 10"><circle cx="5" cy="5" r="4" fill="none" stroke="var(--icon)" stroke-width="1.2"/><path d="M5 2.5V5l1.8 1" stroke="var(--icon)" fill="none"/></svg><span class="label">Time Slots:</span><span class="val time">09/02 – 09/02 (1h 0m)</span></div>
  </article>

  <article class="card assign" style="top:397px">
    <div class="card-head">Subbing For</div>
    <div class="person"><div class="avatar" role="img" aria-label="Staff member photo"></div><span class="name">Owen Tallisford</span>(Teacher)<svg class="edit" width="7" height="7" viewBox="0 0 10 10"><path d="M1 9l1-3 5-5 2 2-5 5z" fill="var(--cyan)"/></svg></div>
    <div class="row"><svg viewBox="0 0 10 12"><path d="M5 0a4 4 0 014 4c0 3-4 8-4 8S1 7 1 4a4 4 0 014-4z" fill="var(--icon)"/><circle cx="5" cy="4" r="1.5" fill="#fff"/></svg><span class="label">Location:</span><span class="val">CHES</span></div>
    <div class="row"><svg viewBox="0 0 10 12"><path d="M1 0h5l3 3v9H1z" fill="var(--icon)"/></svg><span class="label">Status:</span><span class="badge badge--complete">Complete</span></div>
    <div class="row"><svg viewBox="0 0 10 10"><circle cx="5" cy="5" r="4" fill="none" stroke="var(--icon)" stroke-width="1.2"/><path d="M5 2.5V5l1.8 1" stroke="var(--icon)" fill="none"/></svg><span class="label">Time Slots:</span><span class="val time">09/02 – 09/02 (1h 0m)</span></div>
  </article>

  <article class="card assign" style="top:530px">
    <div class="card-head">Subbing For</div>
    <div class="person"><div class="avatar" role="img" aria-label="Staff member photo"></div><span class="name">Caleb Ruvane</span>(Administrator)<svg class="edit" width="7" height="7" viewBox="0 0 10 10"><path d="M1 9l1-3 5-5 2 2-5 5z" fill="var(--cyan)"/></svg></div>
    <div class="row"><svg viewBox="0 0 10 12"><path d="M5 0a4 4 0 014 4c0 3-4 8-4 8S1 7 1 4a4 4 0 014-4z" fill="var(--icon)"/><circle cx="5" cy="4" r="1.5" fill="#fff"/></svg><span class="label">Location:</span><span class="val">CHHS</span></div>
    <div class="row"><svg viewBox="0 0 10 12"><path d="M1 0h5l3 3v9H1z" fill="var(--icon)"/></svg><span class="label">Status:</span><span class="badge badge--active">Active</span></div>
    <div class="row"><svg viewBox="0 0 10 10"><circle cx="5" cy="5" r="4" fill="none" stroke="var(--icon)" stroke-width="1.2"/><path d="M5 2.5V5l1.8 1" stroke="var(--icon)" fill="none"/></svg><span class="label">Time Slots:</span><span class="val time">09/02 – 09/02 (1h 0m)</span></div>
  </article>

  <article class="card assign" style="top:662px">
    <div class="card-head">Subbing For</div>
    <div class="person"><div class="avatar" role="img" aria-label="Staff member photo"></div><span class="name">Lena Brookfield</span>(Teacher)<svg class="edit" width="7" height="7" viewBox="0 0 10 10"><path d="M1 9l1-3 5-5 2 2-5 5z" fill="var(--cyan)"/></svg></div>
    <div class="row"><svg viewBox="0 0 10 12"><path d="M5 0a4 4 0 014 4c0 3-4 8-4 8S1 7 1 4a4 4 0 014-4z" fill="var(--icon)"/><circle cx="5" cy="4" r="1.5" fill="#fff"/></svg><span class="label">Location:</span><span class="val">CHES</span></div>
    <div class="row"><svg viewBox="0 0 10 12"><path d="M1 0h5l3 3v9H1z" fill="var(--icon)"/></svg><span class="label">Status:</span><span class="badge badge--canceled">Canceled</span></div>
    <div class="row"><svg viewBox="0 0 10 10"><circle cx="5" cy="5" r="4" fill="none" stroke="var(--icon)" stroke-width="1.2"/><path d="M5 2.5V5l1.8 1" stroke="var(--icon)" fill="none"/></svg><span class="label">Time Slots:</span><span class="val time">09/02 – 09/02 (1h 0m)</span></div>
  </article>

  <article class="card assign" style="top:794px">
    <div class="card-head">Subbing For</div>
    <div class="person"><div class="avatar" role="img" aria-label="Staff member photo"></div><span class="name">Marcus Delane</span>(Teacher)<svg class="edit" width="7" height="7" viewBox="0 0 10 10"><path d="M1 9l1-3 5-5 2 2-5 5z" fill="var(--cyan)"/></svg></div>
    <div class="row"><svg viewBox="0 0 10 12"><path d="M5 0a4 4 0 014 4c0 3-4 8-4 8S1 7 1 4a4 4 0 014-4z" fill="var(--icon)"/><circle cx="5" cy="4" r="1.5" fill="#fff"/></svg><span class="label">Location:</span><span class="val">CHES</span></div>
    <div class="row"><svg viewBox="0 0 10 12"><path d="M1 0h5l3 3v9H1z" fill="var(--icon)"/></svg><span class="label">Status:</span><span class="badge badge--active">Active</span></div>
    <div class="row"><svg viewBox="0 0 10 10"><circle cx="5" cy="5" r="4" fill="none" stroke="var(--icon)" stroke-width="1.2"/><path d="M5 2.5V5l1.8 1" stroke="var(--icon)" fill="none"/></svg><span class="label">Time Slots:</span><span class="val time">09/02 – 09/02 (1h 0m)</span></div>
  </article>

  <div class="urlbar" style="top:925px">
    <svg class="l" width="10" height="8" viewBox="0 0 10 8"><path d="M0 1h7M0 3h10M0 5h8M0 7h10" stroke="#fff" stroke-width="1.2"/></svg>
    qa.tandemline.test
    <svg class="r" width="9" height="9" viewBox="0 0 10 10"><path d="M8.5 5A3.5 3.5 0 115 1.5h2" fill="none" stroke="#fff" stroke-width="1.6"/><path d="M6 0l3 1.5L6 3.5z" fill="#fff"/></svg>
  </div>
</section>

<section class="screen screen--detail">
  <header class="topbar">
    <svg class="menu-btn" width="10" height="9" viewBox="0 0 10 9"><path d="M0 1h10M0 4.5h10M0 8h10" stroke="#333" stroke-width="1.5"/></svg>
    <div class="brand"><span class="brand-dot"></span>Tandemline</div>
  </header>
  <nav class="nav"><a>Home</a><a>Available Openings</a><a class="is-active">Assignments</a><a>Support</a></nav>

  <article class="card panel" style="top:105px;height:274px">
    <h2>Opening Information</h2>
    <div class="rule"></div>
    <ul class="info">
      <li><span class="k">Summary</span><span class="v">Testing-test</span></li>
      <li><span class="k">Location</span><span class="v">Cedar Hollow Elementary School</span></li>
      <li><span class="k">Type</span><span class="v">Vacancy</span></li>
      <li><span class="k">Regular Staff</span><span class="v"><span class="mini-avatar" role="img" aria-label="Staff member photo"></span>Owen Tallisford</span></li>
      <li><span class="k">Assignment Category</span><span class="v">Teacher</span></li>
      <li><span class="k">Department</span><span class="v"></span></li>
      <li><span class="k">Description</span><span class="v"></span></li>
    </ul>
    <div class="textbox" style="height:66px;margin-top:7px"></div>
  </article>

  <article class="card panel" style="top:394px;height:167px">
    <h2>Comments</h2>
    <div class="rule"></div>
    <div class="textbox" style="height:57px;margin-top:9px;padding:10px;font-size:7px;color:#555">Write a comment or upload a file...</div>
    <div style="display:flex;gap:4px;margin-top:5px">
      <span class="pill pill--blue"><svg width="7" height="7" viewBox="0 0 10 10"><path d="M0 5l10-5-3 10-2-4z" fill="none" stroke="var(--cyan)"/></svg>Post</span>
      <span class="pill pill--blue"><svg width="7" height="7" viewBox="0 0 10 10"><path d="M4 6l2-2M3 5L1 7a1.5 1.5 0 002 2l2-2M7 5l2-2a1.5 1.5 0 00-2-2L5 3" fill="none" stroke="var(--cyan)" stroke-width="1.2"/></svg>Upload</span>
    </div>
    <div style="height:26px;border:1px solid #cfcfcf;margin-top:9px;display:flex;align-items:center;justify-content:center;font-size:7.5px;color:#555">No comments or files uploaded</div>
  </article>

  <article class="card panel" style="top:576px;height:91px">
    <h2>Additional Details</h2>
    <div class="rule"></div>
    <div style="font-size:7.5px;margin-top:7px;color:#444">Parking Spot</div>
    <div style="height:25px;border:1px solid #cfcfcf;margin-top:4px;background:#fff"></div>
  </article>

  <article class="card panel" style="top:682px;height:360px">
    <h2>Time Slots</h2>
    <div class="rule"></div>
    <div style="display:flex;gap:5px;margin-top:7px">
      <span class="pill pill--gray"><svg width="6" height="6" viewBox="0 0 10 10"><rect x="0.5" y="1.5" width="9" height="8" fill="none" stroke="#777"/></svg>Accept</span>
      <span class="pill pill--gray" style="padding:0 6px"><svg width="6" height="6" viewBox="0 0 10 10"><rect x="0.5" y="1.5" width="9" height="8" fill="none" stroke="#777"/></svg>Withdraw</span>
    </div>
    <div class="field-label" style="margin-top:7px"><span class="cb"></span>Date</div>
    <div class="input"><span class="cb"></span>3/19/2026<svg width="8" height="8" viewBox="0 0 10 10"><rect x="0.5" y="1.5" width="9" height="8" fill="none" stroke="#444"/><path d="M0.5 4h9" stroke="#444"/></svg></div>
    <div class="field-label">From</div>
    <div class="input">9:30 am<svg width="8" height="8" viewBox="0 0 10 10"><circle cx="5" cy="5" r="4" fill="none" stroke="#444"/><path d="M5 2.5V5h2" fill="none" stroke="#444"/></svg></div>
    <div class="field-label">To</div>
    <div class="input">9:30 am<svg width="8" height="8" viewBox="0 0 10 10"><circle cx="5" cy="5" r="4" fill="none" stroke="#444"/><path d="M5 2.5V5h2" fill="none" stroke="#444"/></svg></div>
    <p class="meta"><b>Current Assignment:</b> No Assignment</p>
    <p class="meta" style="margin-top:5px"><b>Status:</b> <span class="ok">Active</span></p>
    <div class="input" style="margin-top:20px"><span class="cb"></span>3/19/2026<svg width="8" height="8" viewBox="0 0 10 10"><rect x="0.5" y="1.5" width="9" height="8" fill="none" stroke="#444"/><path d="M0.5 4h9" stroke="#444"/></svg></div>
    <div class="field-label">From</div>
    <div class="input">9:30 am<svg width="8" height="8" viewBox="0 0 10 10"><circle cx="5" cy="5" r="4" fill="none" stroke="#444"/><path d="M5 2.5V5h2" fill="none" stroke="#444"/></svg></div>
    <div class="field-label">To</div>
    <div class="input">9:30 am<svg width="8" height="8" viewBox="0 0 10 10"><circle cx="5" cy="5" r="4" fill="none" stroke="#444"/><path d="M5 2.5V5h2" fill="none" stroke="#444"/></svg></div>
  </article>

  <div class="actions" style="top:1054px">
    <span class="btn btn--save"><svg width="6" height="6" viewBox="0 0 10 10"><rect x="0.5" y="0.5" width="9" height="9" fill="none" stroke="#fff"/><path d="M2.5 5l2 2 3-4" fill="none" stroke="#fff"/></svg>Save</span>
    <span class="btn btn--close"><svg width="6" height="6" viewBox="0 0 10 10"><rect x="0.5" y="0.5" width="9" height="9" fill="none" stroke="#fff"/><path d="M3 3l4 4M7 3l-4 4" stroke="#fff"/></svg>Close</span>
  </div>

  <div class="urlbar" style="top:1091px">
    <svg class="l" width="10" height="8" viewBox="0 0 10 8"><path d="M0 1h7M0 3h10M0 5h8M0 7h10" stroke="#fff" stroke-width="1.2"/></svg>
    qa.tandemline.test
    <svg class="r" width="9" height="9" viewBox="0 0 10 10"><path d="M8.5 5A3.5 3.5 0 115 1.5h2" fill="none" stroke="#fff" stroke-width="1.6"/><path d="M6 0l3 1.5L6 3.5z" fill="#fff"/></svg>
  </div>
</section>

</body>
</html>
```